Coastline Premier Retreats Business Card Design

Design a business card for Coastline Premier Retreats. Look at the website for colors and reference. Card should have logo, name, title, office number, mobile number, email, URL and a tagline like, "Luxury Hotel & Resort Email Marketing" (This might change).

https://www.coastlinepremierretreats.example

The rest I will leave up to your imagination.

Contact Information for Business Card

Logo, name, title, office number, mobile number, email, URL and a tagline like, "Luxury Hotel & Resort Email Marketing" (This might change).

```html
<!DOCTYPE html>
<html lang="en">
<head>
<meta charset="utf-8">
<title>Coastline Premier Retreats – Business Card</title>
<link rel="stylesheet" href="https://fonts.googleapis.com/css2?family=Open+Sans:wght@400;600;700&display=swap">
<style>
  :root {
    --backdrop: #232323;
    --card: #1f1f23;
    --card-back: #1b1b1f;
    --orange: #f37321;
    --white: #ffffff;
    --soft-white: #e6e6e6;
    --emboss: #2a2a2f;
    --divider: #8a8a8a;
  }
  * { box-sizing: border-box; margin: 0; padding: 0; }
  html, body {
    width: 1200px; height: 780px; overflow: hidden;
    background: var(--backdrop);
    font-family: "Open Sans", Arial, sans-serif;
  }
  .canvas { position: relative; width: 1200px; height: 780px; }

  .card {
    position: absolute; top: 235px;
    width: 540px; height: 310px;
    box-shadow: 0 18px 40px rgba(0,0,0,.55);
  }
  .card-front { left: 40px; background: var(--card); }
  .card-back { left: 620px; background: var(--card-back); }

  /* Front */
  .company {
    position: absolute; top: 58px; left: 250px;
    display: flex; align-items: center; gap: 12px;
  }
  .company-mark { width: 16px; height: 16px; background: var(--orange); }
  .company-name {
    color: var(--white); font-weight: 700; font-size: 21px;
    letter-spacing: .5px; line-height: 1.1;
  }

  .person { position: absolute; top: 138px; left: 36px; width: 200px; text-align: right; }
  .person-name { font-size: 26px; font-weight: 700; color: var(--white); line-height: 1.1; }
  .person-name .first { color: var(--orange); }
  .person-title { margin-top: 6px; font-size: 13px; color: var(--soft-white); }

  .divider {
    position: absolute; top: 130px; left: 254px;
    width: 1px; height: 96px; background: var(--divider);
  }

  .contacts { position: absolute; top: 128px; left: 272px; list-style: none; }
  .contacts li {
    display: flex; align-items: center; gap: 10px;
    font-size: 13px; color: var(--soft-white); line-height: 24px;
  }
  .contacts svg { width: 13px; height: 13px; flex: none; }

  .tagline-band {
    position: absolute; left: 0; right: 0; bottom: 16px; height: 34px;
    background: var(--orange);
    display: flex; align-items: center; padding-left: 100px;
  }
  .tagline { color: var(--white); font-size: 14px; }

  /* Back */
  .back-name {
    position: absolute; inset: 0;
    display: flex; align-items: center; justify-content: center;
    color: var(--emboss); font-weight: 700; font-size: 30px; letter-spacing: 1px;
    text-shadow: none;
  }
</style>
</head>
<body>
<main class="canvas">

  <section class="card card-front" aria-label="Business card front">
    <div class="company">
      <span class="company-mark"></span>
      <span class="company-name">Coastline Premier Retreats</span>
    </div>

    <div class="person">
      <p class="person-name"><span class="first">Marisol</span> Vantreck</p>
      <p class="person-title">Co-Founder</p>
    </div>

    <div class="divider"></div>

    <ul class="contacts">
      <li>
        <svg viewBox="0 0 16 16" aria-hidden="true"><path fill="var(--orange)" d="M3.5 1.5l2.5 3-1.5 1.5c.8 2 2.5 3.7 4.5 4.5L10.5 9l3 2.5-1.5 2.5C7 14 2 9 2 3z"/></svg>
        (555) 014-2758
      </li>
      <li>
        <svg viewBox="0 0 16 16" aria-hidden="true"><rect x="4" y="1" width="8" height="14" rx="1.5" fill="none" stroke="var(--orange)" stroke-width="1.5"/></svg>
        (555) 019-7777
      </li>
      <li>
        <svg viewBox="0 0 16 16" aria-hidden="true"><circle cx="8" cy="8" r="6.5" fill="none" stroke="var(--orange)" stroke-width="1.4"/><path d="M1.5 8h13M8 1.5c-3 3.5-3 9.5 0 13M8 1.5c3 3.5 3 9.5 0 13" fill="none" stroke="var(--orange)" stroke-width="1.1"/></svg>
        www.coastlinepremierretreats.example
      </li>
      <li>
        <svg viewBox="0 0 16 16" aria-hidden="true"><rect x="1" y="3" width="14" height="10" fill="var(--orange)"/><path d="M1 3l7 6 7-6" fill="none" stroke="var(--card)" stroke-width="1.3"/></svg>
        info@coastlinepremierretreats.example
      </li>
    </ul>

    <div class="tagline-band">
      <span class="tagline">Luxury Hotel &amp; Resort Email Marketing</span>
    </div>
  </section>

  <section class="card card-back" aria-label="Business card back">
    <p class="back-name">Coastline Premier Retreats</p>
  </section>

</main>
</body>
</html>
```